All-Natural Head Lice Removal company

I need a business card with my pre-existing logo. We are a new company located in Portland Oregon that goes into peoples homes to help with head lice removal. My products and approach are all- natural and also will be around children.On my current logo we used Teal Bl and the color Green. I am open to new ideas just want it simple and creative

Target Market(s)

my biggest market is families of school aged children

Industry/Entity Type

Business

Contact Information for Business Card

see upload for details from previous business card

Font styles to use
Serif

Colors
33a6d7
9bcb3b
f37122

Requirements
Must have
• Basic information/ logo put into a creative format that is catching to the eye
Nice to have
• creative

```html
<!DOCTYPE html>
<html lang="en">
<head>
<meta charset="utf-8">
<title>NitFree Home – Business Card</title>
<link rel="stylesheet" href="https://fonts.googleapis.com/css2?family=Arvo:wght@400;700&display=swap">
<style>
  :root {
    --green: #9bcb3b;
    --green-light: #b3dc6a;
    --green-deep: #86b92c;
    --teal: #33a6d7;
    --ink: #24301a;
    --dark: #222222;
    --white: #ffffff;
    --stage: #ecebe7;
  }
  * { box-sizing: border-box; margin: 0; padding: 0; }
  html, body { width: 1200px; height: 913px; overflow: hidden; }
  body {
    background: var(--stage);
    font-family: "Arvo", Georgia, serif;
    position: relative;
  }
  .card {
    position: absolute;
    top: 306px;
    width: 525px;
    height: 300px;
    border-radius: 4px;
    overflow: hidden;
    box-shadow: 0 6px 18px rgba(0,0,0,.18);
  }
  .card--front {
    left: 50px;
    background: linear-gradient(180deg, var(--green-light) 0%, var(--green) 55%, var(--green-deep) 100%);
  }
  .card--back { left: 625px; background: var(--white); }

  .slogan {
    position: absolute; top: 40px; left: 40px;
    font-size: 16px; color: var(--ink);
  }
  .contact-band {
    position: absolute; top: 96px; left: 0; width: 100%; height: 82px;
    background: var(--white);
  }
  .stripes { position: absolute; display: flex; flex-direction: column; }
  .stripes span { display: block; height: 8px; }
  .stripes--left { left: 0; top: 150px; width: 70px; }
  .stripes--right { right: 0; top: 96px; width: 22px; height: 82px; }
  .stripes--right span { height: 16.4px; }
  .s-teal { background: var(--teal); }
  .s-dark { background: var(--dark); }
  .s-white { background: var(--white); }

  .contact-list {
    position: absolute; top: 108px; right: 36px;
    list-style: none; text-align: right;
    font-size: 14px; line-height: 20px; color: var(--dark);
  }
  .contact-list li { display: flex; justify-content: flex-end; align-items: center; gap: 8px; }
  .contact-list svg { width: 12px; height: 12px; flex: none; }

  .brand { position: absolute; display: flex; align-items: center; gap: 10px; }
  .brand__dot { border-radius: 50%; background: var(--teal); flex: none; }
  .brand__name { font-weight: 700; color: var(--dark); white-space: nowrap; }

  .card--front .brand { left: 40px; top: 214px; }
  .card--front .brand__dot { width: 40px; height: 40px; }
  .card--front .brand__name { font-size: 26px; }

  .person { position: absolute; right: 36px; top: 190px; text-align: right; }
  .person__name { font-size: 18px; color: var(--ink); letter-spacing: .5px; }
  .person__role { font-size: 11px; color: var(--white); letter-spacing: 1px; margin-top: 2px; }

  .card--back .brand { left: 50%; top: 78px; transform: translateX(-50%); }
  .card--back .brand__dot { width: 56px; height: 56px; background: var(--green); }
  .card--back .brand__name { font-size: 40px; }
  .back-text {
    position: absolute; left: 0; width: 100%; top: 190px;
    text-align: center; font-size: 14px; line-height: 19px; color: var(--dark);
  }
  .back-text .tagline { font-weight: 700; }
  .back-text .url { color: var(--teal); }
</style>
</head>
<body>
  <section class="card card--front" aria-label="Business card front">
    <p class="slogan">All Natural In-Home Lice Removal Services</p>
    <div class="contact-band"></div>
    <div class="stripes stripes--left">
      <span class="s-teal"></span><span class="s-dark"></span><span class="s-white"></span><span class="s-teal"></span>
    </div>
    <div class="stripes stripes--right">
      <span class="s-teal"></span><span class="s-dark"></span><span class="s-teal"></span><span class="s-white"></span><span class="s-dark"></span>
    </div>
    <ul class="contact-list">
      <li>1-855-555-0142
        <svg viewBox="0 0 12 12"><path d="M2.5 1 4.5 1 5.3 3.5 4 4.5Q5 7 7.5 8L8.5 6.7 11 7.5 11 9.5Q11 11 9.5 11 1 10.5 1 2.5 1 1 2.5 1Z" fill="#33a6d7"/></svg>
      </li>
      <li>dana@nitfreehome.com
        <svg viewBox="0 0 12 12"><rect x="1" y="2.5" width="10" height="7" fill="none" stroke="#33a6d7" stroke-width="1.2"/><path d="M1 2.5 6 6.5 11 2.5" fill="none" stroke="#33a6d7" stroke-width="1.2"/></svg>
      </li>
      <li>www.nitfreehome.com
        <svg viewBox="0 0 12 12"><circle cx="6" cy="6" r="4.8" fill="none" stroke="#33a6d7" stroke-width="1.1"/><path d="M1.2 6H10.8M6 1.2Q3.5 6 6 10.8M6 1.2Q8.5 6 6 10.8" fill="none" stroke="#33a6d7" stroke-width="1"/></svg>
      </li>
    </ul>
    <div class="brand">
      <span class="brand__dot"></span>
      <span class="brand__name">NitFree Home</span>
    </div>
    <div class="person">
      <p class="person__name">DANA WHITFORD</p>
      <p class="person__role">OWNER</p>
    </div>
  </section>

  <section class="card card--back" aria-label="Business card back">
    <div class="brand">
      <span class="brand__dot"></span>
      <span class="brand__name">NitFree Home</span>
    </div>
    <div class="back-text">
      <p class="tagline">Try NitFree Home Today and Be Lice Free Tomorrow!</p>
      <p class="tagline">All Natural In-Home Lice Removal Services</p>
      <p class="url">www.nitfreehome.com</p>
    </div>
  </section>
</body>
</html>
```